Direct to Consumer extended service contract business with a new disruptive business model needs a

We need a customized wordpress design for a company called 'Bright Harbor Assurance'.
We provide an innovative and unique service contract protection program direct to consumers. This program provides monthly coverage for all electronics purchased in the last 4 years and all electronics the consumer purchases in the future for a low monthly fee. The overall design should communicate a sense of legitimacy, ethics, and superior customer service and support (in an industry that has a huge PR issue to overcome).
Electronics is the first product group, other product groups with different price points to launch in the future..

Target Market(s)

All purchasers of electronic goods...all demographics

Industry/Entity Type

Electronics

Font styles to use
Sans Serif

Requirements
Must have
• Customer Testimonials
Industry News
Customer ratings
Blog posts
Call to action messaging
Like the functional elements and design of quillmesa.example (need to be better)
Nice to have
• Like to see video testimonials
Social network "whats trending related to electronics or service contract industry"
Easy way to register products for warranty

```html
<!DOCTYPE html>
<html lang="en">
<head>
<meta charset="utf-8">
<title>Bright Harbor Assurance – Home Page Layout</title>
<link href="https://fonts.googleapis.com/css2?family=Josefin+Sans:wght@400;600;700&display=swap" rel="stylesheet">
<style>
:root{
  --ink:#2b2219;
  --paper:#ffffff;
  --gold:#e2b21c;
  --gold-dark:#b8860b;
  --brown:#2f251b;
  --sage:#a8bd83;
  --sage-dark:#93aa6c;
  --leaf:#3fae5a;
  --leaf-light:#5cc06f;
  --sand:#d9c7aa;
  --link:#2f9e5a;
}
*{box-sizing:border-box;margin:0;padding:0}
html,body{width:960px;height:1200px;overflow:hidden;background:var(--paper)}
body{position:relative;font-family:"Josefin Sans",Arial,sans-serif;color:var(--ink)}
.abs{position:absolute}
.note{position:absolute;font-size:11px;line-height:13.5px;letter-spacing:.2px;text-transform:uppercase;color:var(--ink)}
.guides{position:absolute;left:0;top:0}
.page{position:absolute;left:310px;top:0;width:340px;height:1200px;background:var(--paper);overflow:hidden}
.hero{position:absolute;left:0;top:0;width:340px;height:137px;background:radial-gradient(ellipse at 50% 40%,#7a6a52 0%,#4a3d2e 45%,#221a12 100%)}
.hero-name{position:absolute;left:0;top:98px;width:340px;text-align:center;font-size:13px;font-weight:600;letter-spacing:1px;color:#d9c79a}
.navbar{position:absolute;left:0;top:136px;width:340px;height:17px;background:var(--gold)}
.nav-brand{position:absolute;left:0;top:0;width:70px;height:17px;background:var(--brown);color:#d9c79a;font-size:4.6px;font-weight:600;padding:6px 0 0 16px;text-transform:uppercase}
.nav-brand::before{content:"";position:absolute;left:7px;top:5px;width:6px;height:6px;border-radius:50%;background:#d9c79a}
.nav-links{position:absolute;left:95px;top:6px;display:flex;gap:10px;font-size:4.6px;color:var(--brown);text-transform:uppercase}
.util{position:absolute;right:6px;top:157px;font-size:4.6px;color:var(--link);display:flex;gap:8px}
.sec-title{position:absolute;left:0;width:340px;text-align:center;font-size:15px;font-weight:400;letter-spacing:.3px;text-transform:uppercase}
.sec-sub{position:absolute;left:0;width:340px;text-align:center;font-size:5.6px;font-weight:400;line-height:8px}
.graph-label{font-family:"Josefin Sans",Arial,sans-serif;font-size:7.5px;fill:var(--ink)}
.graph-tiny{font-family:"Josefin Sans",Arial,sans-serif;font-size:3.4px;fill:var(--ink)}
.plans{position:absolute;left:0;top:336px;width:340px;height:183px;background:var(--brown);color:#fff}
.plan{position:absolute;top:54px;width:74.4px;height:110px;border:2px solid var(--gold);outline:1px solid var(--gold);outline-offset:-4px;text-align:center}
.plan h3{font-size:13px;font-weight:400;margin-top:9px}
.plan p{font-size:5.4px;line-height:8.3px;color:#d8cfc4;margin:6px 5px 0}
.plan .price{font-size:12.5px;margin-top:8px}
.plan .buy{font-size:5.6px;margin-top:3px}
.device{position:absolute;left:22px;top:582px;width:112px;height:100px;background:linear-gradient(160deg,#e6e9ee 0%,#9aa3ad 55%,#2b2f35 100%);border-radius:3px}
.quote{position:absolute;left:161.6px;top:580px;width:166px;height:93px;border:1px solid #cfcfcf;background:#fff}
.quote h4{font-size:11px;font-weight:400;text-align:center;margin-top:6px;letter-spacing:.3px}
.select{position:absolute;left:9px;width:147px;height:15px;border:1px solid #bdbdbd;font-size:7px;padding:4px 0 0 4px}
.select::after{content:"";position:absolute;right:5px;top:5px;border:3.5px solid transparent;border-top:4px solid #222}
.btn{position:absolute;left:9px;top:64px;width:147px;height:16px;background:linear-gradient(#f0c330,var(--gold-dark));color:var(--brown);font-size:10px;text-align:center;padding-top:3px}
.ratings{position:absolute;left:0;top:701px;width:340px;height:182px;background:var(--sage)}
.store{position:absolute;top:49px;width:89px;height:38px;background:var(--sage-dark);border:1px solid #b9cc98}
.store .mark{position:absolute;left:4px;top:6px;width:26px;height:26px;border-radius:50%;background:#2d2d2d;border:2px solid #fff}
.store .red{background:#e04a35}
.store b{position:absolute;left:34px;top:5px;font-size:7px;font-weight:400;color:#2e3a1e;white-space:nowrap}
.store small{position:absolute;left:34px;top:14px;width:52px;font-size:3.4px;line-height:4px;color:#fff}
.store .stars{position:absolute;left:34px;top:26px;font-size:6px;letter-spacing:.3px}
.testi{position:absolute;top:101px;width:50px;height:50px;border-radius:50%;background:linear-gradient(150deg,#8c7a68,#4c5a3b)}
.testi::after{content:"";position:absolute;left:20px;top:16px;border-left:13px solid #fff;border-top:9px solid transparent;border-bottom:9px solid transparent}
.testi::before{content:"";position:absolute;left:11px;top:11px;width:24px;height:24px;border:2px solid #fff;border-radius:50%}
.cap{position:absolute;top:155px;width:66px;text-align:center;font-size:4.2px;line-height:6px;color:#2e3a1e}
.tile{position:absolute;width:73px;height:67px;background:linear-gradient(135deg,var(--leaf-light) 0%,var(--leaf) 50%,#36a04f 100%)}
.tag{position:absolute;right:4px;top:2px;background:var(--gold);color:var(--brown);font-size:3.8px;padding:1px 5px;text-transform:uppercase}
.post{position:absolute;width:73px;text-align:center;font-size:4.2px;color:var(--leaf);text-transform:uppercase}
.footer{position:absolute;left:0;top:1118px;width:340px;height:82px;background:var(--sand)}
.fcol{position:absolute;top:14px;font-size:5px}
.fcol h5{font-size:5.2px;font-weight:700;text-transform:uppercase;border-bottom:1px solid #8b7a63;padding-bottom:2px;width:68px}
.flinks{display:flex;gap:14px;font-size:4.3px;line-height:6px;margin-top:5px;color:#3d3228}
.feed{position:absolute;left:0;top:11px;width:87px;height:45px;background:#fff}
.feed-item{position:relative;height:13.5px;padding:3px 0 0 16px;font-size:3px;line-height:3.6px}
.feed-item::before{content:"";position:absolute;left:4px;top:2px;width:10px;height:10px;border-radius:50%;background:#d9541e}
.feed-item b{color:#c0392b;font-weight:600}
.soc{display:inline-block;width:8px;height:8px;margin-left:2px;vertical-align:-1px}
.copy{position:absolute;left:0;top:1192px;width:340px;height:8px;background:var(--brown);color:#d9c79a;font-size:3.8px;text-align:center;padding-top:2px}
</style>
</head>
<body>

<svg class="guides" width="960" height="1200" viewBox="0 0 960 1200" fill="none" stroke="#2b2219" stroke-width="2.4">
  <path d="M296 22H275V138H296M238 80H275"/>
  <path d="M296 372H275V488H296M238 430H275"/>
  <path d="M296 732H275V848H296M238 790H275"/>
  <path d="M296 965H275V1080H296M238 1022H275"/>
  <path d="M296 1122H275V1192H296M238 1158H275"/>
  <path d="M664 182H684V297H664M684 239H720"/>
  <path d="M664 542H684V657H664M684 598H720"/>
  <path d="M664 745H684V860H664M684 802H720"/>
  <path d="M664 960H684V1076H664M684 1018H720"/>
</svg>

<p class="note" style="left:117px;top:62px">Header<br>The menu header<br>will be fixed</p>
<p class="note" style="left:117px;top:412px">Info about<br>different plans<br>or more features</p>
<p class="note" style="left:149px;top:770px">Customer raiting<br>with stars</p>
<p class="note" style="left:158px;top:1003px">Latest blog<br>posts with<br>atefories</p>
<p class="note" style="left:159px;top:1143px">Footer of<br>website</p>
<p class="note" style="left:730px;top:213px">A graphic to explain<br>the concept of website<br>and what service BHA<br>offering</p>
<p class="note" style="left:730px;top:579px">Take an action after<br>reading and understanding<br>the services above</p>
<p class="note" style="left:730px;top:776px">This area has<br>testimonial videos<br>along with customer<br>raitings</p>
<p class="note" style="left:729px;top:1000px">This area includes<br>industrial news with<br>blog posts</p>

<main class="page">
  <header>
    <div class="hero" role="img" aria-label="Dark leather texture header backdrop"></div>
    <p class="hero-name">Bright Harbor Assurance</p>
    <nav class="navbar">
      <div class="nav-brand">Bright Harbor</div>
      <div class="nav-links"><span>Home</span><span>About us</span><span>Plans</span><span>Take action</span><span>Blog</span><span>News</span><span>FAQ</span><span>Contact us</span></div>
    </nav>
    <div class="util"><span>● log in</span><span>( support</span></div>
  </header>

  <section>
    <h2 class="sec-title" style="top:169px">What we do</h2>
    <p class="sec-sub" style="top:184px">Lorem ipsum nipsum saye losamu Lorem ipsum nipsum saye losamu<br>Lorem ipsum nipsum saye losamu</p>
    <svg class="abs" style="left:0;top:200px" width="340" height="125" viewBox="0 0 340 125">
      <g stroke="#2b2219" stroke-width="1" fill="none">
        <path d="M35.2 37.6L69.6 29.6"/>
        <path d="M35.2 37.6L49.6 72"/>
        <path d="M35.2 37.6L122.4 72.8"/>
        <path d="M122.4 72.8L131.2 40.8"/>
        <path d="M122.4 72.8L157.6 97.6"/>
        <path d="M122.4 72.8L216 55.2"/>
        <path d="M216 55.2L304 92"/>
        <path d="M304 92L304 44"/>
        <path d="M304 92L270.4 108"/>
      </g>
      <g fill="#2b2219">
        <circle cx="69.6" cy="29.6" r="5.5"/><circle cx="49.6" cy="72" r="5.5"/><circle cx="131.2" cy="40.8" r="5.5"/>
        <circle cx="157.6" cy="97.6" r="5.5"/><circle cx="304" cy="44" r="5.5"/><circle cx="270.4" cy="108" r="5.5"/>
      </g>
      <g fill="#2b2219" stroke="#e2b21c" stroke-width="1.6">
        <circle cx="35.2" cy="37.6" r="15"/><circle cx="122.4" cy="72.8" r="15"/><circle cx="216" cy="55.2" r="15"/><circle cx="304" cy="92" r="15"/>
      </g>
      <g fill="#e2b21c">
        <rect x="27" y="33" width="16" height="9" rx="4"/>
        <path d="M118 66h8l-2 3c4 2 5 5 5 8h-14c0-3 1-6 5-8z"/>
        <path d="M209 48h14v7c0 5-4 8-7 10c-3-2-7-5-7-10z"/>
        <rect x="296" y="86" width="16" height="12" rx="2" fill="none" stroke="#e2b21c" stroke-width="1.6"/>
      </g>
      <text class="graph-label" x="13.6" y="19">PURCHASE</text>
      <text class="graph-label" x="103" y="96">PAY BILLS</text>
      <text class="graph-label" x="197" y="35">PROTECT</text>
      <text class="graph-label" x="292" y="115">CLAIM</text>
      <text class="graph-tiny" x="77" y="28">LOW</text><text class="graph-tiny" x="77" y="32">RATES</text>
      <text class="graph-tiny" x="122" y="32">MONTHLY</text>
      <text class="graph-tiny" x="290" y="30">CLAIM YOUR</text><text class="graph-tiny" x="295" y="34">MONEY</text>
      <text class="graph-tiny" x="38" y="84">MORE THAN</text><text class="graph-tiny" x="38" y="88">50000 ITEMS</text>
      <text class="graph-tiny" x="146" y="107">DIFFERENT</text><text class="graph-tiny" x="147" y="111">PACKAGES</text>
      <text class="graph-tiny" x="241" y="106">FIX YOUR</text><text class="graph-tiny" x="241" y="110">BROKEN</text><text class="graph-tiny" x="242" y="114">DEVICE</text>
    </svg>
  </section>

  <section class="plans">
    <h2 class="sec-title" style="top:13px;color:#fff">Our plans</h2>
    <p class="sec-sub" style="top:29px;color:#fff">Lorem ipsum nipsum saye losamu Lorem ipsum nipsum saye losamu<br>Lorem ipsum nipsum saye losamu</p>
    <div class="plan" style="left:12.8px"><h3>GOLD</h3><p>Lorem ipsum nipsum saye losamu Lorem ipsum nipsum saye losamu Lorem ipsum nipsum saye losamu</p><div class="price">$79/M</div><div class="buy">BUY NOW</div></div>
    <div class="plan" style="left:92px"><h3>SILVER</h3><p>Lorem ipsum nipsum saye losamu Lorem ipsum nipsum saye losamu Lorem ipsum nipsum saye losamu</p><div class="price">$179/M</div><div class="buy">BUY NOW</div></div>
    <div class="plan" style="left:171.2px"><h3>BEST</h3><p>Lorem ipsum nipsum saye losamu Lorem ipsum nipsum saye losamu Lorem ipsum nipsum saye losamu</p><div class="price">$109/M</div><div class="buy">BUY NOW</div></div>
    <div class="plan" style="left:250.4px"><h3>SUPERB</h3><p>Lorem ipsum nipsum saye losamu Lorem ipsum nipsum saye losamu Lorem ipsum nipsum saye losamu</p><div class="price">$379/M</div><div class="buy">BUY NOW</div></div>
  </section>

  <section>
    <h2 class="sec-title" style="top:537px">Take action now</h2>
    <p class="sec-sub" style="top:552px">“Pay Less and Claim more on your electronic device Insurance”</p>
    <div class="device" role="img" aria-label="Desktop monitor, tablet and phone showing the website"></div>
    <form class="quote">
      <h4>GET A QUOTE TODAY</h4>
      <div class="select" style="top:22px">Select your mobile phone</div>
      <div class="select" style="top:42px">Select service provider</div>
      <div class="btn">GET QUOTE</div>
    </form>
  </section>

  <section class="ratings">
    <h2 class="sec-title" style="top:17px;color:#2e3a1e">Customer raiting</h2>
    <p class="sec-sub" style="top:31px;color:#2e3a1e">Still confused? check what does our royal customer<br>says about our services</p>
    <div class="store" style="left:17.6px"><span class="mark"></span><b>Orchard Store</b><small>some info came here with description, some info came here</small><span class="stars" style="color:#e0392b">★★★★★</span></div>
    <div class="store" style="left:118px"><span class="mark"></span><b>Riverbend Store</b><small>some info came here with description, some info came here</small><span class="stars" style="color:#2f6fd6">★★★★★</span></div>
    <div class="store" style="left:219px;width:90px"><span class="mark red"></span><b>Globe Store</b><small>some info came here with description, some info came here</small><span class="stars" style="color:#4caf50">★★★★★</span></div>
    <div class="testi" style="left:28.6px" role="img" aria-label="Customer video testimonial"></div>
    <div class="testi" style="left:102px" role="img" aria-label="Customer video testimonial"></div>
    <div class="testi" style="left:175px" role="img" aria-label="Customer video testimonial"></div>
    <div class="testi" style="left:249px" role="img" aria-label="Customer video testimonial"></div>
    <p class="cap" style="left:20.6px">some info came here with description. some info came here with description.</p>
    <p class="cap" style="left:94px">some info came here with description. some info came here with description.</p>
    <p class="cap" style="left:167px">some info came here with description. some info came here with description.</p>
    <p class="cap" style="left:241px">some info came here with description. some info came here with description.</p>
  </section>

  <section>
    <h2 class="sec-title" style="top:898px">Welcome to our blog</h2>
    <p class="sec-sub" style="top:913px">Lorem ipsum nipsum saye losamu Lorem ipsum nipsum saye losamu<br>Lorem ipsum nipsum saye losamu</p>
    <div class="tile" style="left:17.6px;top:939px" role="img" aria-label="Blog post image"><span class="tag">News</span></div>
    <div class="tile" style="left:94.4px;top:939px" role="img" aria-label="Blog post image"><span class="tag">Opinion</span></div>
    <div class="tile" style="left:171.2px;top:939px" role="img" aria-label="Blog post image"><span class="tag">Breaking</span></div>
    <div class="tile" style="left:248px;top:939px" role="img" aria-label="Blog post image"><span class="tag">Gadgets</span></div>
    <p class="post" style="left:17.6px;top:1011px">Post title will came here</p>
    <p class="post" style="left:94.4px;top:1011px">Post title will came here</p>
    <p class="post" style="left:171.2px;top:1011px">Post title will came here</p>
    <p class="post" style="left:248px;top:1011px">Post title will came here</p>
    <div class="tile" style="left:17.6px;top:1025px" role="img" aria-label="Blog post image"><span class="tag">Category</span></div>
    <div class="tile" style="left:94.4px;top:1025px" role="img" aria-label="Blog post image"><span class="tag">Category</span></div>
    <div class="tile" style="left:171.2px;top:1025px" role="img" aria-label="Blog post image"><span class="tag">Category</span></div>
    <div class="tile" style="left:248px;top:1025px" role="img" aria-label="Blog post image"><span class="tag">Category</span></div>
    <p class="post" style="left:17.6px;top:1096px">Post title will came here</p>
    <p class="post" style="left:94.4px;top:1096px">Post title will came here</p>
    <p class="post" style="left:171.2px;top:1096px">Post title will came here</p>
    <p class="post" style="left:248px;top:1096px">Post title will came here</p>
  </section>

  <footer class="footer">
    <div class="fcol" style="left:26px">
      <h5>Welcome to BHA</h5>
      <div class="flinks"><div>Our Plans<br>Benefits<br>About us<br>Contact us</div><div>Blog<br>News<br>Support<br>Terms</div></div>
    </div>
    <div class="fcol" style="left:119px;top:11px">
      <h5 style="width:87px">Social media feed <span class="soc" style="background:#3b5998"></span><span class="soc" style="background:#3aa7e0"></span><span class="soc" style="background:#d62a2a"></span></h5>
      <div class="feed" style="top:16px">
        <div class="feed-item"><b>NAME OF PERSON</b><br>This is an example post in the social feed</div>
        <div class="feed-item"><b>NAME OF PERSON</b><br>This is an example post in the social feed</div>
        <div class="feed-item"><b>NAME OF PERSON</b><br>This is an example post in the social feed</div>
      </div>
    </div>
    <div class="fcol" style="left:232px">
      <h5>Contact us</h5>
      <div style="font-size:3.8px;line-height:4.6px;margin-top:5px;color:#3d3228">
        ⌂ 14 Lantern Way<br>&nbsp;&nbsp;&nbsp;Port Wren 0000<br>☏ Ph: (000) 555-0148<br>✉ Email: hello@brightharbor.example
      </div>
    </div>
  </footer>
  <div class="copy">Copyright © 2014 Bright Harbor Assurance</div>
</main>

</body>
</html>
```